Teeth Whitening Clinic Website Redesign - Social Proof Theme

NEW TEETH SITEREVAMP CURRENT WEBSITE:WWW.SANDIEGOSTEETHWHITENING.COMTHEME:SOCIAL PROOF/5 STAR REVIEWS/TESTIMONIALS THEME:https://maps.example.net/QxRvPLoKzN84 I want a testimonial themed, social proof themed website so customers will be sold by testimonials all over the website….I like a nice clean simple site but with all important factors standing out like CALLS TO ACTIONS, for example the $99 special link in header on original design. Also, testimonials throughout the website placed methodically as not to be FORCED and CLUTTEREDKeep all same exact content for all pages and elements of current design. All buttons, calls to action, navigation, etc. Please do not leave anything out from current design. SPECIAL INSTRUCTIONS for banner image:I want to use actual customer photos inside the banner image in a way that really pops and grabs attention. Please grab some customer photos from my PG Account, fk or rateway account: Also, I want to integrate 5 star rateway logo, friendbook review 5 stars icon, searchly business page 5 stars icon, etc. on the banner as well to show social proof as much as possible. Actual customer photos to be used throughout website:https://www.photogram.example/brightharborsmilestudioplace/ https://www.friendbook.com/SDTeethWhitening/https://www.reviewhub.example/biz/bright-harbor-smile-studio-place-bright-harbor-5 Reviews:https://www.reviewhub.example/biz/bright-harbor-smile-studio-place-bright-harbor-5 https://www.friendbook.com/pg/SDTeethWhitening/reviews/?ref=page_internalhttps://goo.gl/maps/TmJcABLAJwC2 Please do home page first to come up with theme then after approval home page we can move forward additional pages.

Target Market(s)

PEOPLE THAT CARE ABOUT DENTAL HYGEINE AND OR CARE ABOUT THEIR TEETH SMILE

Industry/Entity Type

Dental Clinic

Number of Pages Required

5+ page

Colors

Designer to choose colors to be used in the design.

Requirements
Must have
• NEW TEETH SITE
• REVAMP CURRENT WEBSITE:
• WWW.BRIGHTHARBORSMILESTUDIO.EXAMPLE
• THEME:
• SOCIAL PROOF/5 STAR REVIEWS/TESTIMONIALS THEME:
• https://maps.example.net/QxRvPLoKzN84
• I want a testimonial themed, social proof themed website so customers will be sold by testimonials all over the website….I like a nice clean simple site but with all important factors standing out like CALLS TO ACTIONS, for example the $99 special link in header on original design. Also, testimonials throughout the website placed methodically as not to be FORCED and CLUTTERED
• Keep all same exact content for all pages and elements of current design. All buttons, calls to action, navigation, etc. Please do not leave anything out from current design.
• SPECIAL INSTRUCTIONS for banner image:
• I want to use actual customer photos inside the banner image in a way that really pops and grabs attention. Please grab some customer photos from my PG Account, fk or rateway account:
• Also, I want to integrate 5 star rateway logo, friendbook review 5 stars icon, searchly business page 5 stars icon, etc. on the banner as well to show social proof as much as possible.
• Actual customer photos to be used throughout website:
• https://www.photogram.example/brightharborsmilestudioplace/
• https://www.friendbook.example/BHSmileStudio/
• https://www.reviewhub.example/biz/bright-harbor-smile-studio-place-bright-harbor-5
• Reviews:
• https://www.friendbook.example/pg/BHSmileStudio/reviews/?ref=page_internal
• Please do home page first to come up with theme then after approval home page we can move forward additional pages.
Nice to have
• NEW TEETH SITE
• REVAMP CURRENT WEBSITE:
• THEME:
• Reviews:
Should not have
• NEW TEETH SITE
• REVAMP CURRENT WEBSITE:
• THEME:
• Reviews:

```html
<!DOCTYPE html>
<html lang="en">
<head>
<meta charset="utf-8">
<title>Bright Harbor Smile Studio</title>
<link href="https://fonts.googleapis.com/css2?family=Lato:wght@400;700;900&display=swap" rel="stylesheet">
<style>
:root{
  --blue:#1fb9d9;
  --blue-dark:#1597b5;
  --orange:#f7a700;
  --ink:#2b2b2b;
  --text:#555;
  --gray-bar:#5c5c5c;
  --gray-dark:#3a3a3a;
  --gray-light:#f2f3f4;
  --white:#fff;
}
*{box-sizing:border-box;margin:0;padding:0}
html,body{width:1200px;height:3683px;overflow:hidden}
body{font-family:'Lato',sans-serif;color:var(--text);background:var(--white);position:relative}
section,header,nav,footer,.topbar{position:absolute;left:0;width:1200px}
.abs{position:absolute}
.topbar{top:0;height:36px;background:var(--gray-bar);color:#e6e6e6;font-size:12.5px}
.topbar .info{position:absolute;left:165px;top:10px}
.topbar .book{position:absolute;left:834px;top:0;width:203px;height:36px;background:var(--blue);color:#fff;font-weight:700;font-size:14px;text-align:center;line-height:32px}
.site-header{top:36px;height:94px;background:#fff}
.brand{display:flex;align-items:center;gap:8px}
.brand .mark{width:46px;height:46px;border-radius:50%;border:2px solid #c9d4da;background:#f4f7f9}
.brand .name{color:#5d6770;font-weight:700;font-size:19px;line-height:1.05}
.brand .name span{display:block;font-size:13px;font-weight:700}
.site-header .brand{position:absolute;left:162px;top:22px}
.deal{position:absolute;left:403px;top:28px;font-size:13.5px;color:#444;line-height:19px;font-weight:700}
.deal b{color:var(--blue);font-size:20px}
.address{position:absolute;left:653px;top:28px;font-size:13.5px;color:#444;line-height:19px;font-weight:700}
.phone{position:absolute;left:857px;top:34px;font-size:21px;color:#444;font-weight:700;display:flex;align-items:center;gap:5px}
.main-nav{top:130px;height:58px;background:var(--blue)}
.main-nav ul{list-style:none;display:flex;position:absolute;left:154px;top:0;height:58px}
.main-nav li{color:#fff;font-weight:700;font-size:14px;line-height:58px;padding:0 10px}
.main-nav li.active{background:#5a5a5a;padding:0 20px}
.hero{top:188px;height:527px;background:linear-gradient(90deg,#f7f7f7 0%,#efefef 50%,#f6f6f6 100%)}
.hero h1{position:absolute;left:165px;top:120px;font-size:32px;font-weight:900;line-height:43px;color:var(--ink)}
.hero h1 span{display:block;color:var(--blue)}
.hero .lead{position:absolute;left:167px;top:214px;font-size:19px;line-height:27px;color:#666}
.btn{position:absolute;height:42px;font-size:17px;text-align:center;line-height:40px;font-weight:700}
.btn.primary{left:166px;top:290px;width:157px;background:var(--orange);color:#fff}
.btn.ghost{left:333px;top:290px;width:157px;border:2px solid var(--blue);color:var(--blue);background:#fff}
.review-badge{position:absolute;top:378px;width:120px;text-align:center}
.review-badge .label{font-weight:700;font-size:20px;line-height:26px;color:var(--ink)}
.review-badge .sub{font-size:11px;line-height:14px;color:#777}
.stars{color:var(--orange);font-size:18px;letter-spacing:1px}
.photo{position:absolute;border:8px solid #fff;box-shadow:0 3px 10px rgba(0,0,0,.2)}
.about{top:715px;height:508px}
.about .accent{position:absolute;left:146px;top:102px;width:209px;height:299px;background:var(--blue)}
.about .video{position:absolute;left:162px;top:116px;width:409px;height:269px;background:radial-gradient(circle at 50% 40%,#b5b5b5,#8d8d8d)}
.about .video .play{position:absolute;left:175px;top:105px;width:58px;height:58px;border-radius:50%;background:#fff}
.about .box{position:absolute;left:519px;top:80px;width:515px;height:359px;border:2px solid var(--blue)}
.about h2{position:absolute;left:605px;top:127px;font-size:24px;font-weight:900;line-height:30px;color:var(--ink)}
.about h3{position:absolute;left:605px;top:203px;font-size:18px;color:var(--blue);font-weight:700}
.about p{position:absolute;left:609px;top:241px;width:398px;font-size:13px;line-height:23px;color:#555}
.how{top:1223px;height:551px;overflow:hidden}
.how .photo-area{position:absolute;left:560px;top:0;width:640px;height:551px;background:linear-gradient(120deg,#e8e8e8,#cfc8c2 50%,#9b8f86)}
.how svg.shape{position:absolute;left:0;top:0}
.how h2{position:absolute;left:162px;top:76px;font-size:29px;font-weight:900;color:#fff}
.how p{position:absolute;left:162px;top:125px;width:450px;font-size:12.6px;line-height:19.2px;color:#fff}
.why{top:1774px;height:564px;background:radial-gradient(circle at 50% 50%,#f4f4f4,#e4e4e4)}
.section-title{position:absolute;left:0;width:1200px;text-align:center;font-size:27px;font-weight:900;color:var(--ink)}
.why svg{position:absolute;left:0;top:0}
.why .label{position:absolute;font-size:19px;font-weight:700;color:#444}
.compare{top:2338px;height:522px}
.col{position:absolute;top:125px;height:317px;background:#fff;box-shadow:0 2px 8px rgba(0,0,0,.15)}
.col .head{height:61px;background:var(--gray-dark);color:#fff;font-weight:700;font-size:19px;text-align:center;line-height:58px;position:relative}
.col .head::after{content:"";position:absolute;left:50%;bottom:-10px;margin-left:-10px;border:10px solid transparent;border-bottom:0;border-top-color:var(--blue)}
.col ul{list-style:none;margin-top:2px}
.col li{height:42px;border-bottom:1px solid #e3e3e3;font-size:13px;line-height:42px;padding-left:44px;color:#555;position:relative;white-space:nowrap}
.col li::before{content:"";position:absolute;left:28px;top:17px;width:6px;height:6px;border-top:2px solid var(--blue);border-right:2px solid var(--blue);transform:rotate(45deg)}
.col li:last-child{border-bottom:0}
.col.features{left:162px;width:150px;background:linear-gradient(90deg,#2bc3e0,#1ca9cd)}
.col.features .head{background:none;text-align:left;padding-left:28px;line-height:66px}
.col.features .head::after{display:none}
.col.features li{color:#fff;font-weight:700;border-bottom:1px solid rgba(255,255,255,.3);padding-left:28px}
.col.features li::before{display:none}
.col.ours{left:486px;width:185px;top:113px;height:341px;background:#6b6b6b;z-index:2}
.col.ours .head{background:var(--blue);height:52px;line-height:50px}
.col.ours .head::after{border-top-color:var(--blue)}
.col.ours ul{margin-top:14px}
.col.ours li{color:#fff;font-size:14px;border-bottom:1px solid rgba(255,255,255,.25);padding-left:48px}
.col.ours li::before{border-color:#fff;left:32px}
.testimonials{top:2860px;height:462px;background:var(--gray-dark)}
.testimonials .section-title{color:#fff}
.card{position:absolute;top:151px;width:286px;height:207px;background:#2a2a2a;text-align:center;color:#ccc;font-size:12px;line-height:18px;padding:55px 22px 0}
.card .avatar{position:absolute;left:103px;top:-40px;width:80px;height:80px;border-radius:50%;border:4px solid #2a2a2a;background:linear-gradient(135deg,#9fb3c8,#6d7f91)}
.card .stars{color:#e8262c;font-size:19px;margin-bottom:8px}
.card .who{margin-top:14px;color:#ddd}
.site-footer{top:3322px;height:361px;background:#fff}
.site-footer .brand{position:absolute;left:169px;top:70px}
.social{position:absolute;top:156px;left:173px;display:flex;gap:6px}
.social span{width:32px;height:32px;border-radius:50%;background:#3a4a9a}
.fcol{position:absolute;top:68px}
.fcol h4{color:var(--blue);font-size:19px;font-weight:700;margin-bottom:8px}
.fcol li{list-style:none;font-size:13.5px;line-height:23px;color:#555}
.site-footer .rule{position:absolute;left:162px;top:297px;width:876px;height:1px;background:#ddd}
.site-footer .copy{position:absolute;left:0;width:1200px;top:318px;text-align:center;font-size:11px;color:#666}
</style>
</head>
<body>

<div class="topbar">
  <div class="info">Clinic Open: Mon-Fri 9:15 am to 5:30 pm Sat 10am to 2pm &nbsp;|&nbsp; Book Appointments: Mon-Fri 830 am to 5 pm</div>
  <div class="book">Book Appointment Online</div>
</div>

<header class="site-header">
  <div class="brand"><div class="mark"></div><div class="name">Bright Harbor<span>Smile Studio</span></div></div>
  <div class="deal">Click Here to Get Our <b>$99</b> Teeth<br>Whiting Deal (Reg: $378)</div>
  <div class="address">410 Harbor View Blvd #205<br>Bright Harbor, CA 90010</div>
  <div class="phone"><svg width="20" height="20" viewBox="0 0 24 24"><path fill="#1fb9d9" d="M6.6 10.8a15 15 0 0 0 6.6 6.6l2.2-2.2a1 1 0 0 1 1-.25 11.4 11.4 0 0 0 3.6.6 1 1 0 0 1 1 1V20a1 1 0 0 1-1 1A17 17 0 0 1 3 4a1 1 0 0 1 1-1h3.5a1 1 0 0 1 1 1c0 1.25.2 2.45.6 3.6a1 1 0 0 1-.25 1z"/></svg>1-555-014-2290</div>
</header>

<nav class="main-nav">
  <ul>
    <li class="active">HOME</li><li>OUR PROCESS</li><li>PHOTOS</li><li>FREE TREATMENTS</li><li>TESTIMONIALS</li><li>BLOG</li><li>FAQ</li><li>CONTACT</li><li>GIFT CERTIFICATES</li>
  </ul>
</nav>

<section class="hero">
  <h1><span>GET THAT WHITE SMILE</span>YOU’VE ALWAYS WANTED</h1>
  <p class="lead">Amazing Results, The Most Effective System,<br>More Affordable Than The Dentist</p>
  <div class="btn primary">Book Online</div>
  <div class="btn ghost">Contact Us</div>
  <div class="review-badge" style="left:156px"><div class="label">Rateway</div><div class="sub">Reviews</div><div class="stars">★★★★★</div></div>
  <div class="review-badge" style="left:283px"><div class="label">Searchly</div><div class="sub">Business</div><div class="stars">★★★★★</div></div>
  <div class="review-badge" style="left:425px"><div class="label">Friendbook</div><div class="sub">Reviews</div><div class="stars">★★★★★</div></div>

  <div class="photo" role="img" aria-label="Customer selfie with staff" style="left:661px;top:34px;width:123px;height:122px;background:linear-gradient(135deg,#d8d2cc,#a89c92)"></div>
  <div class="photo" role="img" aria-label="Smiling customer holding a sign" style="left:854px;top:34px;width:144px;height:127px;background:linear-gradient(135deg,#c7b9a5,#8a6f74)"></div>
  <div class="photo" role="img" aria-label="Two customers smiling" style="left:572px;top:134px;width:143px;height:136px;background:linear-gradient(135deg,#e0d7cc,#b59a7d)"></div>
  <div class="photo" role="img" aria-label="Customers posing with staff" style="left:925px;top:160px;width:122px;height:122px;background:linear-gradient(135deg,#d6cfcb,#8b4f68)"></div>
  <div class="photo" role="img" aria-label="Two friends showing white smiles" style="left:727px;top:105px;width:179px;height:172px;background:linear-gradient(135deg,#c9b39c,#6f5a4c)"></div>
  <div class="photo" role="img" aria-label="Happy couple after whitening" style="left:611px;top:251px;width:163px;height:172px;background:linear-gradient(135deg,#b9b0a8,#5e5550)"></div>
  <div class="photo" role="img" aria-label="Group of smiling customers" style="left:782px;top:291px;width:242px;height:172px;background:linear-gradient(135deg,#ddd0c0,#a0806a)"></div>
</section>

<section class="about">
  <div class="accent"></div>
  <div class="video" role="img" aria-label="Clinic introduction video"><div class="play"><svg width="58" height="58" viewBox="0 0 58 58"><path d="M23 18 L40 29 L23 40Z" fill="#222"/></svg></div></div>
  <div class="box"></div>
  <h2>BRIGHT HARBOR’S TEETH<br>WHITENING CENTER</h2>
  <h3>THE BEST PRICE, SERVICE AND RESULTS.</h3>
  <p>Bright Harbor’s Teeth Whitening Center features state-of-the-art technologies that are safe, industry-unique and very cost-effective. Our teeth whitening system utilizes the latest blue light whitening technology. Our Blue Light Systems are calibrated precisely for optimal activation of our exclusive hydrogen peroxide based whitening solution which is manufactured in a FDA registered facility in the USA.</p>
</section>

<section class="how">
  <div class="photo-area" role="img" aria-label="Smiling customers holding Smile With Cheer and Best Patient Ever signs"></div>
  <svg class="shape" width="700" height="551" viewBox="0 0 700 551"><path d="M0 0H586C690 150 690 400 586 551H0Z" fill="#1fb9d9"/></svg>
  <h2>HOW IT WORKS</h2>
  <p>We have a very effective teeth whitening treatment that is guaranteed to get you quick results in about 1 hour. To start the treatment you’ll apply a Hydrogen Peroxide based whitening agent to your teeth. We then place our cold blue light directly in front of your exposed teeth for 15 minutes per treatment. The lighting systems we use activate the whitening agent and thats what accelerates the whitening process, giving you whiter teeth in less than an hour. We always perform what we call a “Triple Treatment”. So that’s 3 of the 15 minute treatments all done consecutively, in the same visit. The actual whitening time is a total of 45 minutes. Now there is a few minute break in between each 15 minute treatment and this is why we tell all of our patients to give yourself one hour at the office. The biggest benefit of doing an in office treatment vs a take home kit is that you will see results immediately after the treatment. We also include our home maintenance kit for after care. It’s very important that no matter where you get your teeth whitened, you need to maintain them for long lasting results. You’ll use our maintenance kit once or twice per month as a touch up to help maintain your newly whitened teeth, and that ultimately make your results last longer.</p>
</section>

<section class="why">
  <div class="section-title" style="top:52px">WHY CHOOSE US</div>
  <svg width="1200" height="564" viewBox="0 0 1200 564">
    <circle cx="606" cy="286" r="176" fill="none" stroke="#dcdcdc" stroke-width="4"/>
    <circle cx="606" cy="286" r="129" fill="#fff"/>
    <circle cx="606" cy="230" r="28" fill="#eef3f6" stroke="#c9d4da" stroke-width="2"/>
    <text x="606" y="300" text-anchor="middle" font-family="Lato,sans-serif" font-weight="700" font-size="22" fill="#5d6770">Bright Harbor</text>
    <text x="606" y="322" text-anchor="middle" font-family="Lato,sans-serif" font-weight="700" font-size="15" fill="#5d6770">Smile Studio</text>
    <g fill="#fff" stroke="#f28c00" stroke-width="5">
      <circle cx="476" cy="147" r="9"/><circle cx="432" cy="286" r="9"/><circle cx="523" cy="410" r="9"/>
      <circle cx="729" cy="147" r="9"/><circle cx="778" cy="286" r="9"/><circle cx="698" cy="406" r="9"/>
    </g>
    <g fill="#1fb9d9">
      <circle cx="409" cy="145" r="37"/><circle cx="372" cy="290" r="37"/><circle cx="485" cy="454" r="37"/>
      <circle cx="800" cy="138" r="37"/><circle cx="837" cy="290" r="37"/><circle cx="737" cy="454" r="37"/>
    </g>
    <g fill="none" stroke="#fff" stroke-width="2.5" stroke-linecap="round" stroke-linejoin="round">
      <path d="M397 160 L390 153 L410 133 L424 131 L422 145 L402 165Z"/><circle cx="416" cy="139" r="2.5"/>
      <circle cx="372" cy="290" r="16"/><path d="M372 290 L382 280 M362 296 L382 296"/>
      <circle cx="485" cy="454" r="18"/><path d="M477 459 Q485 467 493 459"/><circle cx="479" cy="448" r="1.5"/><circle cx="491" cy="448" r="1.5"/>
      <circle cx="800" cy="128" r="9"/><path d="M784 156 Q786 140 800 140 Q814 140 816 156Z"/>
      <circle cx="837" cy="290" r="18"/><path d="M828 290 L835 297 L847 283"/>
      <path d="M727 442 Q737 436 747 442 Q752 452 746 462 L742 470 L738 460 L734 470 L729 462 Q722 452 727 442Z"/>
    </g>
  </svg>
  <div class="label" style="right:848px;top:134px">PRICE</div>
  <div class="label" style="right:872px;top:279px">RESULTS</div>
  <div class="label" style="right:766px;top:447px">NO PAIN</div>
  <div class="label" style="left:846px;top:126px">BEST DOCTOR</div>
  <div class="label" style="left:886px;top:279px">CONVENIENCE</div>
  <div class="label" style="left:784px;top:443px">SERVICE</div>
</section>

<section class="compare">
  <div class="section-title" style="top:48px">COMPARE US</div>
  <div class="col features"><div class="head">FEATURES</div>
    <ul><li>SPEED</li><li>EASE OF USE</li><li>COST</li><li>AVAILABILITY</li><li>PAIN</li></ul></div>
  <div class="col" style="left:312px;width:171px"><div class="head">GLOWLINE</div>
    <ul><li>1-2 Hours</li><li>Difficult / Dentist</li><li>$300 - $600</li><li>Limited Availability</li><li>Pain &amp; Sensitivity</li></ul></div>
  <div class="col ours"><div class="head">BRIGHT HARBOR’S</div>
    <ul><li>45 Mins</li><li>Very Easy</li><li>$378</li><li>Appt Only</li><li>No Pain</li></ul></div>
  <div class="col" style="left:672px;width:175px"><div class="head">LUMAWHITE</div>
    <ul><li>7-14 Days</li><li>Difficult / Dentist</li><li>$300 - $600</li><li>Limited Availability</li><li>Sensitivity</li></ul></div>
  <div class="col" style="left:851px;width:174px"><div class="head">HOME KITS</div>
    <ul><li>7-30 Days</li><li>Difficult</li><li>$50 - $150</li><li>Store Purchase</li><li>Sensitivity</li></ul></div>
</section>

<section class="testimonials">
  <div class="section-title" style="top:47px">TESTIMONIALS</div>
  <div class="card" style="left:157px"><div class="avatar" role="img" aria-label="Customer photo"></div><div class="stars">★★★★★</div>My God they are great and Lively :)<br>Kind and love the result!!!!!!!<br>Definitely going back!!!:)<div class="who">Mina S.<br>Seaview, CA</div></div>
  <div class="card" style="left:456px"><div class="avatar" role="img" aria-label="Customer photo" style="background:linear-gradient(135deg,#b08aa0,#6d4f63)"></div><div class="stars">★★★★★</div>I went with my husband and niece as a group to get our teeth whitened and we were all pleased with the results.<div class="who">Lena G.<br>Bright Harbor, CA</div></div>
  <div class="card" style="left:755px"><div class="avatar" role="img" aria-label="Customer photo" style="background:linear-gradient(135deg,#e8c05a,#c25a4a)"></div><div class="stars">★★★★★</div>My teeth look fabulous!!! I’ve been here twice already and the staff is kind, thorough, and just plain awesome!<div class="who">Rosa R.<br>Bright Harbor, CA</div></div>
  <svg class="abs" style="left:92px;top:218px" width="30" height="56" viewBox="0 0 30 56"><path d="M26 2 L4 28 L26 54" fill="none" stroke="#bbb" stroke-width="3"/></svg>
  <svg class="abs" style="left:1064px;top:218px" width="30" height="56" viewBox="0 0 30 56"><path d="M4 2 L26 28 L4 54" fill="none" stroke="#bbb" stroke-width="3"/></svg>
</section>

<footer class="site-footer">
  <div class="brand"><div class="mark"></div><div class="name">Bright Harbor<span>Smile Studio</span></div></div>
  <div class="social"><span></span><span style="background:#3a8fd6"></span><span style="background:#3b4a7a"></span><span style="background:#2f6aa8"></span></div>
  <div class="fcol" style="left:458px"><h4>QUICK LINKS</h4><ul><li>Home</li><li>Book Appointment Online</li><li>Our Process</li><li>Photos</li><li>Testimonials</li><li>Blog</li></ul></div>
  <div class="fcol" style="left:675px"><h4>SUBLINKS</h4><ul><li>FAQ</li><li>Contact</li><li>Gift Certificates</li><li>After Care</li><li>Consent Form Espanol</li></ul></div>
  <div class="fcol" style="left:880px"><h4>RESOURCES</h4><ul><li>Consent Form English</li><li>Cancellation Policy</li><li>Privacy Policy</li><li>Free Treatments</li></ul></div>
  <div class="rule"></div>
  <div class="copy">© 2018 Company Name &nbsp;All right reserved &nbsp;Term of Use</div>
</footer>

</body>
</html>
```